Web Design Services Create a Similar website to my Competitor

We would like a similar website designed like our main competitor with all the features there website has and more. Also we would like to accept payments through our website and to rank quickly with seo based on our home page and other page use of high traffic keywords. this is the website we would like to have ours designed similar to https://www.harbourpetalstudio.com. we will be providing the same services and more just at a different location. We would also like to know be able to easily make adjustments to the website when its time to edit it please thanks.

Basically I am looking to have have similar website built almost exactly the same but with my logo, and other personalized information to my company Rosalind Marigold Beauty Lounge. I will need to send you model images and logo design idea but the body and user interface of my competitor https://www.harbourpetalstudio.com will be exactly the same. I can be reached anytime to answer any questions you may have.
Updates

Hi Designers I would like to clarify some information Harbour Petal Studio is my Competitor we are not affiliated. I would like my website to be designed similar to hers but please do not take any content from her website to put on mine I will be providing images to be posted on my website. Also please do not use any of her videos or YouTube videos on my website to avoid any legal issues. Thanks for your understanding.

Target Market(s)

Make up Application Services For Events and Lindenbrook Summer Festival

Industry/Entity Type

Beauty and Makeup Application and services

Coding

Coded - Design and coding required

Number of Pages Required

5+ page

Font styles to use
Sans Serif

Colors
E54698
E96AAD
F1A4CE
F9D9EA
FCEFF6
A7469A
B969AE
D3A5CF
EDDBEB
F8F0F9

Requirements
Must have
• Must be similar to my competitor, need a video section, testimonial and must be easily able to navigate to information sections and book now payment notifications running on all pages so customers can easily book there spot for 2026 carnival
Nice to have
• I am looking to have a similar website to https://www.harbourpetalstudio.com created but make it as minimal and modern
Should not have
• Project can be coded if it makes it easier to create a similar look to my competitor just ask that updates can easily be made later on.

```html
<!DOCTYPE html>
<html lang="en">
<head>
<meta charset="utf-8">
<title>Rosalind Marigold Beauty Lounge</title>
<link rel="stylesheet" href="https://fonts.googleapis.com/css2?family=Montserrat:wght@400;500;600;700;800;900&display=swap">
<style>
:root{
  --magenta:#d8287f;
  --pink:#e54698;
  --pink-mid:#e88bc4;
  --pink-soft:#e9a2cf;
  --blush:#f6e9f3;
  --blush-row:#f5e8f2;
  --ink:#111111;
  --text:#333333;
  --muted:#666666;
  --white:#ffffff;
}
*{box-sizing:border-box;margin:0;padding:0}
html,body{width:1200px;height:4348px;overflow:hidden}
body{position:relative;font-family:"Montserrat",sans-serif;color:var(--text);background:var(--white)}
.abs{position:absolute}
.btn{position:absolute;display:flex;align-items:center;justify-content:center;background:var(--magenta);color:var(--white);font-weight:800;text-transform:uppercase;letter-spacing:.3px;white-space:nowrap}
.section-title{position:absolute;left:0;width:1200px;text-align:center;font-weight:900;font-size:30px;color:var(--ink);letter-spacing:.3px}
.section-title em{font-style:normal;color:var(--magenta)}
.rule{position:absolute;height:3px;width:48px;background:var(--magenta);left:576px}
.photo{position:absolute}
.arrow{position:absolute;width:44px;height:44px;border-radius:50%;border:2px solid #777;display:flex;align-items:center;justify-content:center}

/* header */
.brand{position:absolute;left:130px;top:36px;width:264px;text-align:center;font-weight:600;color:var(--ink);white-space:nowrap}
.brand .name{font-size:24px;line-height:32px;letter-spacing:-.3px}
.brand .sub{font-size:17px;line-height:26px;margin-top:4px;font-weight:500}
.search{position:absolute;left:668px;top:30px;width:168px;height:36px;border:1.5px solid #555;display:flex;align-items:center;padding-left:14px;font-size:12px;color:#444}
.search svg{position:absolute;right:10px;top:9px}
.call{position:absolute;left:860px;top:28px;display:flex;gap:14px;align-items:center}
.call .lbl{font-size:14px;color:#333}
.call .num{font-size:18px;color:var(--ink);font-weight:500}
.nav{position:absolute;left:410px;top:84px;display:flex;gap:0;font-size:13.5px;color:#333;white-space:nowrap}
.nav a{display:block;padding:6px 10px;text-decoration:none;color:inherit;margin-right:4px}
.nav a.active{background:var(--pink);color:var(--white)}

/* hero */
.hero{position:absolute;left:0;top:135px;width:1200px;height:568px;background:linear-gradient(90deg,#6d6170 0%,#8c7a86 30%,#a2655f 55%,#2c4f8f 75%,#c79a3f 100%)}
.hero h1{position:absolute;left:152px;top:90px;font-weight:900;font-size:54px;line-height:63px;color:var(--white);text-transform:uppercase;letter-spacing:.5px}
.hero h1 em{font-style:normal;color:var(--pink-soft)}
.hero p{position:absolute;left:153px;top:308px;width:440px;font-size:17px;line-height:27px;color:var(--white);font-weight:600}
.dots{position:absolute;display:flex;gap:12px}
.dots i{width:8px;height:8px;border-radius:50%;background:var(--white);display:block}

/* events */
.event{position:absolute;top:845px;width:216px;height:318px;background:var(--white);box-shadow:0 4px 16px rgba(0,0,0,.12)}
.event .photo{left:0;top:0;width:216px;height:213px}
.event .date{position:absolute;left:19px;top:230px;font-size:14px;font-weight:600;color:var(--ink)}
.event .desc{position:absolute;left:19px;top:258px;width:160px;font-size:12.5px;line-height:18px;color:var(--ink);font-weight:500}

/* lounge */
.lounge{position:absolute;left:0;top:1287px;width:1200px;height:562px;background:var(--blush)}
.lounge h2{position:absolute;left:0;top:52px;width:1200px;text-align:center;font-weight:900;font-size:29px;line-height:41px;color:var(--ink)}
.lounge h2 em{font-style:normal;color:var(--magenta)}
.lounge p{position:absolute;left:260px;top:150px;width:680px;text-align:center;font-size:12.5px;line-height:20px;color:#333}
.services{position:absolute;left:140px;top:290px;width:920px;height:105px;display:flex}
.service{flex:1 1 auto;display:flex;flex-direction:column;align-items:center;justify-content:flex-start;gap:14px;border-right:1.5px solid #d9c4d4;font-size:13.5px;font-weight:600;color:var(--ink);white-space:nowrap}
.service:last-child{border-right:none}

/* testimonials */
.t-frame{position:absolute;left:148px;top:2012px;width:904px;height:326px;background:var(--pink-mid)}
.t-card{position:absolute;top:14px;width:284px;height:296px;background:var(--white)}
.t-card .stars{position:absolute;left:30px;top:30px;display:flex;gap:3px}
.t-card p{position:absolute;left:30px;top:68px;width:228px;font-size:11px;line-height:17.6px;color:#444}
.t-card .av{position:absolute;left:30px;top:238px;width:38px;height:38px;border-radius:50%;background:radial-gradient(circle,#b06a3a,#3a2420)}
.t-card .who{position:absolute;left:82px;top:240px;font-size:11.5px;font-weight:700;color:var(--ink)}
.t-card .when{position:absolute;left:82px;top:258px;font-size:10.5px;color:#666}
.pdots{position:absolute;top:2374px;left:554px;display:flex;gap:10px}
.pdots i{width:10px;height:10px;border-radius:50%;background:#d9d9d9;display:block}
.pdots i.on{background:var(--magenta)}

/* video */
.video-band{position:absolute;left:0;top:2442px;width:1200px;height:507px;background:var(--blush)}
.video-box{position:absolute;left:150px;top:2517px;width:341px;height:343px;background:var(--white)}
.video-box h2{position:absolute;left:36px;top:34px;width:290px;font-weight:900;font-size:23px;line-height:30px;color:var(--ink);white-space:nowrap}
.video-box h2 em{font-style:normal;color:var(--magenta);display:block}
.video-box .bar{position:absolute;left:36px;top:142px;width:48px;height:3px;background:var(--magenta)}
.video-box p{position:absolute;left:36px;top:162px;width:270px;font-size:12.5px;line-height:19px;color:#333}

/* faq */
.faq{position:absolute;left:150px;width:902px;height:38px;background:var(--blush-row);display:flex;align-items:center;padding-left:24px;font-size:15px;color:#222}
.faq svg{position:absolute;right:14px;top:10px}

/* cta band */
.cta{position:absolute;left:0;top:3451px;width:1200px;height:554px;background:var(--magenta)}
.cta h2{position:absolute;left:0;top:52px;width:1200px;text-align:center;font-weight:900;font-size:29.5px;line-height:42px;color:var(--white)}
.cta .btn{background:var(--white);color:var(--magenta)}
.cta .photo{top:300px;width:218px;height:210px}
.cta .arrow{border-color:var(--white)}

/* footer */
.footer{position:absolute;left:0;top:4005px;width:1200px;height:343px;background:var(--blush)}
.footer .brand{top:50px;left:140px;width:244px}
.footer .brand .name{font-size:22px;line-height:30px}
.footer .brand .sub{font-size:16px;line-height:24px;margin-top:6px}
.footer h4{position:absolute;font-size:12.5px;font-weight:700;color:var(--ink);line-height:18px;white-space:nowrap}
.footer .line{position:absolute;font-size:12px;color:#333;line-height:17px;white-space:nowrap}
.menu{position:absolute;left:681px;top:73px;font-size:12px;line-height:17.4px;color:#333;list-style:none}
.social{position:absolute;left:194px;top:190px;display:flex;gap:5px}
.social i{width:24px;height:24px;border-radius:50%;background:var(--magenta);display:block}
.email-field{position:absolute;left:799px;top:105px;width:253px;height:43px;border:1px solid #999;background:var(--white);display:flex;align-items:center;padding-left:42px;font-size:12px;color:#333}
.email-field svg{position:absolute;left:16px;top:15px}
.divider{position:absolute;left:150px;top:263px;width:902px;height:1px;background:#cbb7c6}
.copy{position:absolute;left:0;top:290px;width:1200px;text-align:center;font-size:11.5px;color:#333}
</style>
</head>
<body>

<!-- Header -->
<header>
  <div class="brand"><div class="name">Rosalind Marigold</div><div class="sub">Beauty Lounge</div></div>
  <div class="search">Search
    <svg width="16" height="16" viewBox="0 0 16 16" fill="none" stroke="#333" stroke-width="1.6"><circle cx="7" cy="7" r="5"/><path d="M11 11l4 4"/></svg>
  </div>
  <div class="call">
    <svg width="30" height="30" viewBox="0 0 30 30" fill="none" stroke="#d8287f" stroke-width="1.6"><circle cx="15" cy="15" r="13.5"/><path d="M10.5 8.5c-1 .8-1.6 2-1 3.8 1.3 3.6 4.2 6.5 7.8 7.9 1.8.6 3-.1 3.8-1l-2.3-2.4-2 1c-1.6-.8-3-2.2-3.8-3.8l1-2z"/></svg>
    <div><div class="lbl">Call Us</div><div class="num">+1 555 014 2290</div></div>
  </div>
  <nav class="nav">
    <a class="active">Home</a><a>About Us</a><a>Anywhere</a><a>Store</a><a>Trindad</a><a>Jamaica</a><a>Gallery</a><a>Blog</a><a>Contact us</a>
  </nav>
</header>

<!-- Hero -->
<section class="hero" role="img" aria-label="Smiling carnival performer in a jewelled feather headdress with colourful plumes">
  <h1>Get <em>Carnival</em> -<br>Ready with<br>Rosalind</h1>
  <p>Lorem ipsum dolor sit amet, consectetur adipiscing elit, sed do eiusmod tempor incididunt ut labore et dolore magna aliqua.</p>
  <div class="btn" style="left:152px;top:421px;width:303px;height:58px;font-size:16px;">Choose your destination</div>
  <div class="dots" style="left:562px;top:523px"><i></i><i></i><i></i><i></i></div>
</section>

<!-- Events -->
<h2 class="section-title" style="top:744px">OUR EVENTS</h2>
<div class="rule" style="top:803px"></div>
<div class="arrow" style="left:55px;top:971px"><svg width="14" height="14" viewBox="0 0 14 14" fill="none" stroke="#555" stroke-width="1.8"><path d="M9 2L4 7l5 5"/></svg></div>
<div class="arrow" style="left:1097px;top:971px"><svg width="14" height="14" viewBox="0 0 14 14" fill="none" stroke="#555" stroke-width="1.8"><path d="M5 2l5 5-5 5"/></svg></div>
<article class="event" style="left:148px"><div class="photo" role="img" aria-label="Carnival dancer in gold sequined costume" style="background:linear-gradient(135deg,#c89b3a,#6b4a2a 60%,#b8a37a)"></div><div class="date">14 May 2025</div><div class="desc">Lorem ipsum dolor sit amet, consectetur</div></article>
<article class="event" style="left:376px"><div class="photo" role="img" aria-label="Carnival performer in orange feathered headdress" style="background:linear-gradient(135deg,#e08a1e,#8a3a1a 60%,#d9a030)"></div><div class="date">14 May 2025</div><div class="desc">Lorem ipsum dolor sit amet, consectetur</div></article>
<article class="event" style="left:604px"><div class="photo" role="img" aria-label="Group of carnival dancers in blue and orange feathers" style="background:linear-gradient(135deg,#1f3a6b,#c06a2a 55%,#2a2a3a)"></div><div class="date">14 May 2025</div><div class="desc">Lorem ipsum dolor sit amet, consectetur</div></article>
<article class="event" style="left:834px"><div class="photo" role="img" aria-label="Carnival crowd at night with feathered costumes" style="background:linear-gradient(135deg,#2a3d6a,#d08a3a 55%,#5a2e3a)"></div><div class="date">14 May 2025</div><div class="desc">Lorem ipsum dolor sit amet, consectetur</div></article>
<div class="btn" style="left:525px;top:1200px;width:150px;height:40px;font-size:12px;">See packages</div>

<!-- Lounge -->
<section class="lounge">
  <h2>WITH <em>ROSALIND MARIGOLD?</em> IT'S A LUXURY<br>PREP LOUNGE, NOT A PANIC ROOM.</h2>
  <p>Sed ut perspiciatis unde omnis iste natus error sit voluptatem accusantium doloremque laudantium, totam rem aperiam, eaque ipsa quae ab illo inventore veritatis et quasi architecto beatae vitae dicta sunt explicabo. Nemo enim ipsam voluptatem quia voluptas sit aspernatur aut odit aut fugit</p>
  <div class="rule" style="top:234px"></div>
  <div class="services">
    <div class="service"><svg width="56" height="56" viewBox="0 0 56 56" fill="none" stroke="#d8287f" stroke-width="2"><path d="M8 26c6-4 14-4 20 2 6-6 14-6 20-2-1 10-6 14-12 14-4 0-6-3-8-5-2 2-4 5-8 5-6 0-11-4-12-14z"/><path d="M28 22l-5-10M28 22l5-10M28 22V8"/></svg>Pro Makeup</div>
    <div class="service"><svg width="56" height="56" viewBox="0 0 56 56" fill="none" stroke="#d8287f" stroke-width="2"><path d="M10 50V26C10 14 18 6 28 6s18 8 18 20v24"/><path d="M18 50V28c0-6 4-10 10-10s10 4 10 10v22"/></svg>Carnival Hair</div>
    <div class="service"><svg width="56" height="56" viewBox="0 0 56 56" fill="none" stroke="#d8287f" stroke-width="2"><rect x="6" y="16" width="44" height="30" rx="3"/><path d="M20 16l3-6h10l3 6"/><circle cx="28" cy="31" r="9"/><circle cx="28" cy="31" r="4"/></svg>Photoshoot</div>
    <div class="service"><svg width="56" height="56" viewBox="0 0 56 56" fill="none" stroke="#d8287f" stroke-width="2"><rect x="8" y="8" width="36" height="40" rx="3"/><rect x="14" y="14" width="36" height="36" rx="3"/><path d="M28 26v12l10-6z"/></svg>Reels</div>
    <div class="service"><svg width="56" height="56" viewBox="0 0 56 56" fill="none" stroke="#d8287f" stroke-width="2"><rect x="10" y="6" width="36" height="40" rx="4"/><path d="M10 28h36M14 14h28v10H14z"/><circle cx="18" cy="36" r="3"/><circle cx="38" cy="36" r="3"/><path d="M16 46v5M40 46v5"/></svg>Shuttle</div>
    <div class="service"><svg width="56" height="56" viewBox="0 0 56 56" fill="none" stroke="#d8287f" stroke-width="2"><rect x="8" y="6" width="40" height="44"/><path d="M28 6v44M8 28h40M13 14h10M33 14h10M13 36h10M33 36h10"/></svg>Dressing Rooms</div>
    <div class="service"><svg width="56" height="56" viewBox="0 0 56 56" fill="none" stroke="#d8287f" stroke-width="2"><circle cx="28" cy="18" r="9"/><path d="M12 50c0-10 7-16 16-16s16 6 16 16"/><path d="M40 24h8v6h-8z"/></svg>Refreshments</div>
  </div>
  <div class="btn" style="left:503px;top:452px;width:194px;height:56px;font-size:15px;">Yes I need this</div>
</section>

<!-- Testimonials -->
<h2 class="section-title" style="top:1904px">CUSTOMER <em>TESTIMONIALS</em></h2>
<div class="t-frame">
  <div class="t-card" style="left:14px">
    <div class="stars"><svg width="96" height="18" viewBox="0 0 96 18" fill="#d8287f"><path id="st" d="M9 1l2.4 5.2 5.6.6-4.2 3.8 1.2 5.6L9 13.4 4 16.2l1.2-5.6L1 6.8l5.6-.6z"/><use href="#st" x="19"/><use href="#st" x="38"/><use href="#st" x="57"/><use href="#st" x="76"/></svg></div>
    <p>Sed ut perspiciatis unde omnis iste natus error sit voluptatem accu santium dolor emque laudantium, totam rem aperiam, eaque ipsa quae ab illo inventore veritatis et quasi architecto beatae vitae dicta sunt explicabo. Nemo enim ipsam volu ptatem quia voluptas sit aspernatur aut odit aut fugit.</p>
    <div class="av" role="img" aria-label="Customer portrait"></div><div class="who">DANA WHITFIELD</div><div class="when">2 Days Ago</div>
  </div>
  <div class="t-card" style="left:310px">
    <div class="stars"><svg width="96" height="18" viewBox="0 0 96 18" fill="#d8287f"><use href="#st"/><use href="#st" x="19"/><use href="#st" x="38"/><use href="#st" x="57"/><use href="#st" x="76"/></svg></div>
    <p>Sed ut perspiciatis unde omnis iste natus error sit voluptatem accu santium dolor emque laudantium, totam rem aperiam, eaque ipsa quae ab illo inventore veritatis et quasi architecto beatae vitae dicta sunt explicabo. Nemo enim ipsam volu ptatem quia voluptas sit aspernatur aut odit aut fugit.</p>
    <div class="av" role="img" aria-label="Customer portrait"></div><div class="who">DANA WHITFIELD</div><div class="when">2 Days Ago</div>
  </div>
  <div class="t-card" style="left:606px">
    <div class="stars"><svg width="96" height="18" viewBox="0 0 96 18" fill="#d8287f"><use href="#st"/><use href="#st" x="19"/><use href="#st" x="38"/><use href="#st" x="57"/><use href="#st" x="76"/></svg></div>
    <p>Sed ut perspiciatis unde omnis iste natus error sit voluptatem accu santium dolor emque laudantium, totam rem aperiam, eaque ipsa quae ab illo inventore veritatis et quasi architecto beatae vitae dicta sunt explicabo. Nemo enim ipsam volu ptatem quia voluptas sit aspernatur aut odit aut fugit.</p>
    <div class="av" role="img" aria-label="Customer portrait"></div><div class="who">DANA WHITFIELD</div><div class="when">2 Days Ago</div>
  </div>
</div>
<div class="pdots"><i class="on"></i><i></i><i></i><i></i><i></i></div>

<!-- Video -->
<section class="video-band"></section>
<div class="photo" role="img" aria-label="Video still: artist painting a child's face for carnival" style="left:445px;top:2496px;width:607px;height:404px;background:linear-gradient(120deg,#5a3a2a,#b58a6a 40%,#e6d6d8 55%,#6a4a3a 80%,#3a2a22)">
  <svg class="abs" style="left:268px;top:167px" width="70" height="70" viewBox="0 0 70 70"><circle cx="35" cy="35" r="33" fill="#d8287f"/><path d="M28 22v26l21-13z" fill="#fff"/></svg>
</div>
<div class="video-box">
  <h2>ROSALIND MARIGOLD <em>SLOTS DISAPPEAR</em><em>FAST</em></h2>
  <div class="bar"></div>
  <p>Sed ut perspiciatis unde omnis iste natus error sit voluptatem accusantium doloremque laudantium, totam rem aperiam, eaque ipsa quae ab illo</p>
  <div class="btn" style="left:40px;top:256px;width:204px;height:42px;font-size:12.5px;">See availability now</div>
</div>

<!-- FAQ -->
<h2 class="section-title" style="top:2999px">FAQS</h2>
<div class="rule" style="top:3050px"></div>
<div class="faq" style="top:3108px">Do I have to pay all of the money upfront<svg width="20" height="20" viewBox="0 0 20 20" fill="none" stroke="#d8287f" stroke-width="1.4"><circle cx="10" cy="10" r="8.5"/><path d="M10 5.5v9M5.5 10h9"/></svg></div>
<div class="faq" style="top:3157px">Can I pay on the day?<svg width="20" height="20" viewBox="0 0 20 20" fill="none" stroke="#d8287f" stroke-width="1.4"><circle cx="10" cy="10" r="8.5"/><path d="M10 5.5v9M5.5 10h9"/></svg></div>
<div class="faq" style="top:3206px">What if I miss my appointment?<svg width="20" height="20" viewBox="0 0 20 20" fill="none" stroke="#d8287f" stroke-width="1.4"><circle cx="10" cy="10" r="8.5"/><path d="M10 5.5v9M5.5 10h9"/></svg></div>
<div class="faq" style="top:3255px">Do you accept walk-ins?<svg width="20" height="20" viewBox="0 0 20 20" fill="none" stroke="#d8287f" stroke-width="1.4"><circle cx="10" cy="10" r="8.5"/><path d="M10 5.5v9M5.5 10h9"/></svg></div>
<div class="faq" style="top:3304px">Can I choose my makeup artist?<svg width="20" height="20" viewBox="0 0 20 20" fill="none" stroke="#d8287f" stroke-width="1.4"><circle cx="10" cy="10" r="8.5"/><path d="M10 5.5v9M5.5 10h9"/></svg></div>
<div class="faq" style="top:3353px">Do you have a time guide?<svg width="20" height="20" viewBox="0 0 20 20" fill="none" stroke="#d8287f" stroke-width="1.4"><circle cx="10" cy="10" r="8.5"/><path d="M10 5.5v9M5.5 10h9"/></svg></div>

<!-- CTA -->
<section class="cta">
  <h2>STILL THINKING? THE GIRLS WHO BOOKED<br>ALREADY KNOW - THE ROAD HITS DIFFERENT<br>WHEN ROSALIND MARIGOLD BEHIND THE SCENES.</h2>
  <div class="btn" style="left:449px;top:230px;width:302px;height:57px;font-size:15px;">Choose your destination</div>
  <div class="arrow" style="left:70px;top:374px"><svg width="14" height="14" viewBox="0 0 14 14" fill="none" stroke="#fff" stroke-width="1.8"><path d="M9 2L4 7l5 5"/></svg></div>
  <div class="arrow" style="left:1081px;top:374px"><svg width="14" height="14" viewBox="0 0 14 14" fill="none" stroke="#fff" stroke-width="1.8"><path d="M5 2l5 5-5 5"/></svg></div>
  <div class="photo" role="img" aria-label="Masked carnival reveller in ruffled costume" style="left:150px;background:linear-gradient(135deg,#c44a7a,#e0a03a 50%,#3a5a8a)"></div>
  <div class="photo" role="img" aria-label="Festival-goer with painted face at night" style="left:377px;background:linear-gradient(135deg,#3a2a22,#b06a3a 50%,#e0a050)"></div>
  <div class="photo" role="img" aria-label="Carnival performer with blue feathered headpiece" style="left:605px;background:linear-gradient(135deg,#2a6ac0,#d8d0c8 50%,#e08a3a)"></div>
  <div class="photo" role="img" aria-label="Laughing carnival dancer in red costume" style="left:834px;background:linear-gradient(135deg,#8a1a1a,#d04a2a 50%,#e0a060)"></div>
</section>

<!-- Footer -->
<footer class="footer">
  <div class="brand"><div class="name">Rosalind Marigold</div><div class="sub">Beauty Lounge</div></div>
  <h4 style="left:224px;top:152px">FOLLOW US</h4>
  <div class="social"><i></i><i></i><i></i><i></i><i></i></div>

  <h4 style="left:423px;top:50px">CONTACT US</h4>
  <svg class="abs" style="left:424px;top:82px" width="12" height="16" viewBox="0 0 12 16" fill="#d8287f"><path d="M6 0a6 6 0 0 0-6 6c0 4.5 6 10 6 10s6-5.5 6-10a6 6 0 0 0-6-6zm0 8.5A2.5 2.5 0 1 1 6 3.5a2.5 2.5 0 0 1 0 5z"/></svg>
  <div class="line" style="left:449px;top:80px">42 Orchard Lane, Suite 310<br>Lindenbrook, TN 37199</div>
  <svg class="abs" style="left:424px;top:145px" width="13" height="13" viewBox="0 0 13 13" fill="#d8287f"><path d="M2.6.5L5 3 3.8 4.6c.8 1.7 2.3 3.2 4 4L9.4 7.4 12 9.8 10.6 12C5.4 12.4.6 7.6 1 2.4z"/></svg>
  <div class="line" style="left:449px;top:143px">+1 555 014 2290</div>
  <svg class="abs" style="left:424px;top:181px" width="14" height="11" viewBox="0 0 14 11" fill="#d8287f"><path d="M0 0h14v11H0z"/><path d="M1.5 1.5L7 6l5.5-4.5" stroke="#f6e9f3" stroke-width="1.3" fill="none"/></svg>
  <div class="line" style="left:449px;top:178px">hello@RosalindMarigold.com</div>

  <h4 style="left:679px;top:50px">MENU</h4>
  <ul class="menu"><li>Home</li><li>About Us</li><li>Anywhere</li><li>Store</li><li>Trindad</li><li>Jamaica</li><li>Gallery</li><li>Blog</li><li>Contact us</li></ul>

  <h4 style="left:797px;top:50px">SUBSCRIBE TO GET<br>EXCLUSIVE UPDATES</h4>
  <div class="email-field"><svg width="14" height="11" viewBox="0 0 14 11"><rect width="14" height="11" fill="#222"/><path d="M1.5 1.5L7 6l5.5-4.5" stroke="#fff" stroke-width="1.3" fill="none"/></svg>Email id</div>
  <div class="btn" style="left:799px;top:170px;width:253px;height:45px;font-size:17px;font-weight:600;background:var(--magenta)">Subscribe</div>

  <div class="divider"></div>
  <div class="copy">Copyright © 2025 All Rights Reserved</div>
</footer>

</body>
</html>
```